Website for Excavator and Earthworks Company

We require a modern, sleek and practical website for our newly created earthworks/excavator business in Perth, Western Australia called Bluegum Ridge Earthworks.

The website should have a modern, cutting edge feel but only needs to be relatively simplistic in it's layout and eventual functionality.

Some pages it should have would be Home, About, Projects and Contact Us.

```html
<!DOCTYPE html>
<html lang="en">
<head>
<meta charset="UTF-8">
<title>Bluegum Ridge Earthworks</title>
<link href="https://fonts.googleapis.com/css2?family=Michroma&family=Rubik:wght@400;500;600;700&display=swap" rel="stylesheet">
<style>
:root{
  --lime:#c9db00;
  --ink:#0d0d0d;
  --white:#ffffff;
  --soft:#f6f6f6;
  --grey:#d0ccc6;
  --text:#333333;
  --line:#e3e3e3;
  --night:#1c2b3d;
}
*{margin:0;padding:0;box-sizing:border-box}
html,body{width:1200px;height:3743px;overflow:hidden;background:var(--white)}
body{position:relative;font-family:'Rubik',sans-serif;color:var(--ink)}
.abs{position:absolute}
.display{font-family:'Michroma',sans-serif;font-weight:400;text-transform:uppercase;line-height:1.15;color:var(--ink)}
.btn{position:absolute;display:flex;align-items:center;justify-content:center;font:600 12px 'Rubik',sans-serif;text-transform:uppercase;text-decoration:none;color:var(--ink);clip-path:polygon(6% 0,100% 0,94% 100%,0 100%)}
.btn--lime{background:var(--lime)}
.btn--black{background:var(--ink);color:var(--white)}
.btn--white{background:var(--white)}
.brand{display:flex;align-items:center;gap:10px}
.brand__mark{width:22px;height:22px;background:var(--lime)}
.brand__name{font:600 15px 'Rubik',sans-serif;text-transform:uppercase;letter-spacing:.5px;color:var(--ink);line-height:1.1}
.nav{display:flex;gap:26px}
.nav a{font:600 11px 'Rubik',sans-serif;text-transform:uppercase;color:var(--ink);text-decoration:none}
.body-copy{font-size:11.5px;line-height:17.5px;color:var(--text)}
.photo{position:absolute}
/* hero */
.hero{position:absolute;left:0;top:61px;width:1200px;height:522px;background:linear-gradient(90deg,#cdc9c3,#d6d2cc)}
.hero__machine{left:516px;top:26px;width:684px;height:496px;background:radial-gradient(ellipse at 55% 50%,#e5b81c 0%,#b99020 35%,#3a3a38 62%,rgba(208,204,198,0) 80%)}
.hero h1{left:64px;top:142px;font-size:44px}
.hero p{left:64px;top:295px;width:380px;font-size:12px;line-height:17px;color:var(--ink)}
/* services */
.card{position:absolute;top:1188px;width:263px;height:188px;background:var(--soft)}
.card__icon{position:absolute;left:38px;top:-29px;width:58px;height:58px;border-radius:50%;background:var(--ink);display:flex;align-items:center;justify-content:center}
.card h3{position:absolute;left:38px;top:54px;font:600 13.5px 'Rubik',sans-serif;text-transform:uppercase}
.card p{position:absolute;left:38px;top:75px;width:200px;font-size:11px;line-height:17.5px;color:var(--text)}
/* stats */
.stat{position:absolute;display:flex;gap:10px}
.stat b{display:block;font:500 24px 'Rubik',sans-serif;line-height:28px}
.stat span{display:block;font-size:11px;line-height:15px;color:var(--text);margin-top:4px}
/* form */
.field-label{position:absolute;font:500 11px 'Rubik',sans-serif;color:var(--ink)}
.field{position:absolute;background:var(--white);font-size:10px;color:#666;padding-left:12px;display:flex;align-items:center}
</style>
</head>
<body>

<!-- header -->
<header>
  <div class="abs brand" style="left:64px;top:18px">
    <div class="brand__mark"></div>
    <div class="brand__name">Bluegum Ridge<br><span style="font-size:9px;letter-spacing:2px">Earthworks</span></div>
  </div>
  <nav class="abs nav" style="left:477px;top:25px">
    <a href="#">Home</a><a href="#">About</a><a href="#">Projects</a><a href="#">Contact Us</a>
  </nav>
  <a class="btn btn--lime" href="#" style="left:970px;top:12px;width:166px;height:38px">Get a Quote</a>
</header>

<!-- hero -->
<section class="hero">
  <div class="photo hero__machine" role="img" aria-label="Yellow front-end wheel loader with raised bucket"></div>
  <h1 class="abs display">Moving Earth.<br>Building<br>Foundations.</h1>
  <p class="abs">Providing expert earthworks, excavation, and site preparation services with precision, safety, and efficiency.</p>
  <a class="btn btn--black" href="#" style="left:64px;top:343px;width:166px;height:39px">Get a Quote</a>
  <a class="btn btn--white" href="#" style="left:232px;top:343px;width:168px;height:39px">View Our Projects</a>
</section>

<!-- about -->
<section>
  <div class="abs" style="left:153px;top:767px;width:364px;height:298px;background:var(--lime)"></div>
  <div class="photo" role="img" aria-label="Yellow boom lift beside a corrugated building at sunset" style="left:171px;top:677px;width:452px;height:369px;background:linear-gradient(180deg,#8a8fb0 0%,#c8a9a6 35%,#9aa2ad 60%,#c9a629 80%,#5a6472 100%)"></div>
  <h2 class="abs display" style="left:716px;top:680px;font-size:31px;line-height:38px">About<br>Bluegum Ridge</h2>
  <div class="abs" style="left:494px;top:768px;width:530px;height:2px;background:var(--lime)"></div>
  <div class="abs body-copy" style="left:716px;top:794px;width:318px">
    <p>Founded in Perth, Western Australia, Bluegum Ridge Earthworks brings together decades of experience in the excavation and earthmoving industry. Our team of certified operators and project managers are committed to delivering exceptional results for every client.</p>
    <p style="margin-top:17px">We pride ourselves on our commitment to safety, environmental responsibility, and customer satisfaction. Using state-of-the-art equipment and proven techniques, we tackle projects ranging from small residential jobs to large-scale commercial developments.</p>
  </div>
  <a class="btn btn--lime" href="#" style="left:716px;top:1007px;width:141px;height:39px">About Us</a>
</section>

<!-- services -->
<section>
  <div class="card" style="left:177px">
    <div class="card__icon"><svg width="30" height="30" viewBox="0 0 30 30"><path d="M3 25 L13 11 L19 19 L22 15 L28 25Z" fill="#fff"/><circle cx="21" cy="7" r="3" fill="#fff"/></svg></div>
    <h3>Site Preparation</h3>
    <p>Expert site preparation services ensuring stable foundations, precise grading, and readiness for residential and commercial construction projects.</p>
  </div>
  <div class="card" style="left:468px">
    <div class="card__icon"><svg width="30" height="30" viewBox="0 0 30 30" fill="none" stroke="#fff" stroke-width="2"><rect x="12" y="14" width="12" height="7"/><path d="M12 16 L7 6 L3 13"/><rect x="11" y="22" width="14" height="4" rx="2"/></svg></div>
    <h3>Excavation</h3>
    <p>Expert excavation solutions providing safe, efficient earthmoving for foundations, trenches, and site developments.</p>
  </div>
  <div class="card" style="left:758px">
    <div class="card__icon"><svg width="32" height="30" viewBox="0 0 32 30" fill="none" stroke="#fff" stroke-width="2"><path d="M3 10 L21 10 L21 20 L3 20Z"/><path d="M21 13 L27 13 L29 17 L29 20 L21 20"/><circle cx="8" cy="22" r="2.5"/><circle cx="24" cy="22" r="2.5"/></svg></div>
    <h3>Earthmoving</h3>
    <p>Expert earthmoving solutions ensuring accurate bulk excavation, levelling, and site preparation for construction projects.</p>
  </div>
</section>

<!-- stats -->
<section>
  <div class="photo" role="img" aria-label="Excavator and dump trucks under a stormy sky" style="left:0;top:1470px;width:1200px;height:451px;background:linear-gradient(180deg,#16263a 0%,#2f4866 55%,#4a5560 75%,#8c7440 100%)"></div>
  <div class="abs display" style="left:177px;top:1540px;width:847px;text-align:center;font-size:56px;line-height:70px;color:transparent;-webkit-text-stroke:1px rgba(255,255,255,.25);white-space:nowrap;letter-spacing:2px">Bluegum Ridge</div>
  <div class="abs" style="left:177px;top:1668px;width:292px;height:331px;background:var(--lime)">
    <div class="abs brand__name" style="left:40px;top:48px;font-size:18px">Bluegum Ridge</div>
    <div class="abs" style="left:40px;top:243px;font:600 19px/26px 'Rubik',sans-serif;text-transform:uppercase">25+ Years of<br>Undefeated Success</div>
  </div>
  <div class="abs" style="left:469px;top:1668px;width:552px;height:331px;background:var(--soft)">
    <div class="abs" style="left:279px;top:60px;width:1px;height:210px;background:var(--line)"></div>
    <div class="abs" style="left:82px;top:165px;width:390px;height:1px;background:var(--line)"></div>
  </div>
  <div class="stat" style="left:550px;top:1733px">
    <svg width="34" height="34" viewBox="0 0 34 34" fill="none" stroke="#111" stroke-width="1.8"><circle cx="15" cy="15" r="11"/><circle cx="15" cy="15" r="5"/><path d="M17 17 L28 28"/></svg>
    <div><b>205+</b><span>Successfully finished<br>projects</span></div>
  </div>
  <div class="stat" style="left:790px;top:1733px">
    <svg width="34" height="34" viewBox="0 0 34 34" fill="none" stroke="#111" stroke-width="1.8"><circle cx="17" cy="13" r="10"/><circle cx="17" cy="13" r="4" fill="#111"/><path d="M11 21 L8 32 L13 29 L15 33 M23 21 L26 32 L21 29 L19 33"/></svg>
    <div><b>25+</b><span>Year of experience<br>with pride</span></div>
  </div>
  <div class="stat" style="left:550px;top:1866px">
    <svg width="34" height="34" viewBox="0 0 34 34" fill="none" stroke="#111" stroke-width="1.8"><circle cx="17" cy="17" r="14" stroke-dasharray="3 2"/><path d="M17 9 L17 17 L23 20"/></svg>
    <div><b>24/7</b><span>Round-the-Clock<br>Availability</span></div>
  </div>
  <div class="stat" style="left:790px;top:1866px">
    <svg width="34" height="34" viewBox="0 0 34 34" fill="none" stroke="#111" stroke-width="1.8"><circle cx="17" cy="17" r="14" stroke-dasharray="3 2"/><circle cx="17" cy="17" r="8" fill="#111"/><path d="M24 24 L30 30"/></svg>
    <div><b>98%</b><span>On-Time<br>Completion Rate</span></div>
  </div>
</section>

<!-- projects -->
<section>
  <h2 class="abs display" style="left:0;top:2085px;width:1200px;text-align:center;font-size:30px">Recent Projects</h2>
  <p class="abs body-copy" style="left:400px;top:2128px;width:400px;text-align:center">Take a look at some of our recent earthworks and excavation projects across Perth and Western Australia.</p>
  <div class="photo" role="img" aria-label="Tracked excavator on muddy ground" style="left:113px;top:2189px;width:231px;height:311px;background:linear-gradient(160deg,#c7922e 0%,#6d5d4c 40%,#8b7663 100%)"></div>
  <div class="photo" role="img" aria-label="Yellow bulldozer facing forward on a dirt site" style="left:362px;top:2189px;width:475px;height:311px;background:linear-gradient(180deg,#6a6d70 0%,#d89a25 45%,#2f3330 70%,#6b5544 100%)"></div>
  <div class="photo" role="img" aria-label="Excavator digging beside a rocky slope" style="left:856px;top:2189px;width:229px;height:311px;background:linear-gradient(160deg,#8d8780 0%,#c8a038 50%,#6f6255 100%)"></div>
  <div class="photo" role="img" aria-label="Orange excavators parked on a flat work site" style="left:113px;top:2521px;width:475px;height:311px;background:linear-gradient(180deg,#c6cfd6 0%,#d9a056 50%,#8a7564 100%)"></div>
  <div class="photo" role="img" aria-label="Tracked loader working on rock piles" style="left:607px;top:2521px;width:230px;height:311px;background:linear-gradient(180deg,#b7bcc0 0%,#d99327 45%,#3c3a37 100%)"></div>
  <div class="photo" role="img" aria-label="Row of yellow dump trucks on a red dirt site" style="left:856px;top:2521px;width:229px;height:311px;background:linear-gradient(180deg,#8ea0ad 0%,#c7ad5e 50%,#a97d5b 100%)"></div>
  <a class="btn btn--lime" href="#" style="left:517px;top:2865px;width:166px;height:38px">View Our Projects</a>
</section>

<!-- quote -->
<section>
  <div class="photo" role="img" aria-label="Excavator on dark soil under a cloudy sky" style="left:0;top:3044px;width:1200px;height:450px;background:linear-gradient(180deg,#3e4650 0%,#5c6168 50%,#a86f2a 72%,#4a3328 100%)"></div>
  <div class="abs" style="left:318px;top:2997px;width:562px;height:544px;background:var(--lime)"></div>
  <h2 class="abs display" style="left:375px;top:3047px;font-size:30px">Get a Quote</h2>
  <p class="abs" style="left:375px;top:3093px;width:430px;font-size:11px;line-height:16px">Ready to start your earthworks project? Get in touch with our team for a free, no-obligation quote.</p>
  <div class="field-label" style="left:375px;top:3143px">Full Name</div>
  <div class="field-label" style="left:606px;top:3143px">Email Address</div>
  <div class="field" style="left:375px;top:3160px;width:218px;height:38px">Enter your name</div>
  <div class="field" style="left:606px;top:3160px;width:218px;height:38px">Enter email</div>
  <div class="field-label" style="left:375px;top:3213px">Phone Number</div>
  <div class="field-label" style="left:606px;top:3213px">Service Required</div>
  <div class="field" style="left:375px;top:3231px;width:218px;height:38px">Phone number</div>
  <div class="field" style="left:606px;top:3231px;width:218px;height:38px">Select a service
    <svg class="abs" style="right:12px;top:15px" width="10" height="8" viewBox="0 0 10 8"><path d="M1 2 L5 6 L9 2" fill="none" stroke="#111" stroke-width="1.5"/></svg>
  </div>
  <div class="field-label" style="left:375px;top:3283px">Project Details</div>
  <div class="field" style="left:375px;top:3301px;width:449px;height:131px"></div>
  <a class="abs" href="#" style="left:375px;top:3446px;width:449px;height:38px;background:var(--ink);color:var(--white);display:flex;align-items:center;justify-content:center;font:600 11px 'Rubik',sans-serif;text-transform:uppercase;text-decoration:none">Get a Quote</a>
</section>

<!-- footer -->
<footer>
  <div class="abs brand" style="left:177px;top:3590px">
    <div class="brand__mark" style="width:30px;height:30px"></div>
    <div class="brand__name" style="font-size:19px">Bluegum Ridge<br><span style="font-size:11px;letter-spacing:3px">Earthworks</span></div>
  </div>
  <nav class="abs nav" style="left:637px;top:3604px;gap:52px">
    <a href="#">Home</a><a href="#">About</a><a href="#">Projects</a><a href="#">Contact Us</a>
  </nav>
  <div class="abs" style="left:177px;top:3676px;width:844px;height:1px;background:var(--line)"></div>
  <p class="abs" style="left:0;top:3700px;width:1200px;text-align:center;font-size:11px;color:var(--text)">Copyright © 2026 Bluegum Ridge. All Rights Reserved.</p>
</footer>

</body>
</html>
```